Bry7Legal Letterhead

Need a new letterhead for my law firm.
IDENTIFYING INFORMATION BELOW:
Anselmo R Quintara III
Attorney at Law
Address: 2847 Larkspur Blvd, Ste 300, Dallas, TX 75204
Phone: 877-482-6017
Fax: 469-738-1452
Email: bry@bry7legal.example
Website: www.bry7legal.example

Colors
0054AA
0677BA
7BADD7
CADEEF
E8F1F8

Requirements
Must have
• Logo needs to be on the letterhead, along with identifying information which is included in the project description.

```html
<!DOCTYPE html>
<html lang="en">
<head>
<meta charset="utf-8">
<title>Bry7Legal Letterhead</title>
<link rel="stylesheet" href="https://fonts.googleapis.com/css2?family=Arimo:wght@400&family=Source+Sans+3:wght@400;600;700&display=swap">
<style>
  :root {
    --ink: #1c1c1c;
    --brand-deep: #0054aa;
    --brand-mid: #0677ba;
    --brand-light: #7badd7;
    --brand-pale: #cadeef;
    --backdrop: #d9d9d9;
    --paper: #fbfbfb;
  }
  * { margin: 0; padding: 0; box-sizing: border-box; }
  html, body { width: 1200px; height: 1013px; overflow: hidden; background: var(--backdrop); }
  .letterhead {
    position: absolute; left: 268px; top: 31px;
    width: 663px; height: 950px;
    background: var(--paper);
    box-shadow: 0 10px 30px rgba(0,0,0,.25);
    font-family: "Arimo", Arial, sans-serif;
    color: var(--ink);
  }
  .brand { position: absolute; left: 74px; top: 50px; }
  .brand-name {
    display: flex; align-items: center; gap: 10px;
    font-family: "Source Sans 3", sans-serif; font-weight: 700;
    font-size: 44px; line-height: 1; color: var(--ink); letter-spacing: 1px;
  }
  .brand-mark { width: 18px; height: 18px; background: var(--brand-mid); }
  .brand-tagline {
    margin: 6px 0 0 44px;
    font-family: "Source Sans 3", sans-serif; font-weight: 400;
    font-size: 18px; letter-spacing: 2.5px; text-transform: uppercase;
  }
  .letter-body { position: absolute; left: 74px; top: 184px; width: 518px; }
  .letter-body p {
    font-size: 13.1px; line-height: 16.3px; text-align: justify;
    margin-bottom: 41px;
  }
  .signature { position: absolute; left: 40px; top: 737px; }
  .signature-rule { width: 236px; height: 1px; background: var(--brand-deep); margin-bottom: 14px; }
  .signature-name {
    font-family: "Source Sans 3", sans-serif; font-weight: 600;
    font-size: 19.5px; letter-spacing: 1px; text-transform: uppercase;
  }
  .signature-title {
    font-family: "Source Sans 3", sans-serif; font-weight: 400;
    font-size: 13.5px; letter-spacing: 3.5px; text-transform: uppercase; margin-top: 2px;
  }
  .contact-list { list-style: none; margin-top: 18px; }
  .contact-list li {
    display: flex; align-items: center; gap: 8px;
    font-size: 10.8px; line-height: 18.5px; letter-spacing: .3px;
  }
  .contact-list svg { width: 8px; height: 8px; fill: var(--brand-deep); flex: none; }
  .footer-band {
    position: absolute; left: 0; bottom: 12px; width: 663px; height: 9px;
    display: flex; flex-direction: column;
  }
  .footer-band-main { flex: 1; background: var(--brand-deep); }
  .footer-band-accent { height: 3px; background: var(--brand-light); }
</style>
</head>
<body>
  <main class="letterhead">
    <header class="brand">
      <div class="brand-name"><span class="brand-mark"></span>BRY7LEGAL</div>
      <div class="brand-tagline">Law in Motion</div>
    </header>

    <section class="letter-body">
      <p>Lorem ipsum dolor sit amet, consectetur adipisicing elit, sed do eiusmod tempor incididunt ut labore et dolore magna aliqua. Ut enim ad minim veniam, quis nostrud exercitation ullamco laboris nisi ut aliquip ex ea commodo consequat. Duis aute irure dolor in reprehenderit in voluptate velit esse cillum dolore eu fugiat nulla pariatur. Excepteur sint occaecat cupidatat non proident, sunt in culpa qui officia deserunt mollit anim id est laborum. Sed ut perspiciatis unde omnis iste natus error sit voluptatem accusantium doloremque laudantium, totam rem aperiam, eaque ipsa quae ab illo inventore veritatis et quasi architecto beatae vitae dicta sunt explicabo. Nemo enim ipsam voluptatem quia voluptas sit aspernatur aut odit aut fugit, sed quia consequuntur magni dolores eos qui ratione voluptatem sequi nesciunt. Neque porro voluptatem sequi nesciunt. Nemo enim ipsam voluptatem quia voluptas.</p>
      <p>Lorem ipsum dolor sit amet, consectetur adipisicing elit, sed do eiusmod tempor incididunt ut labore et dolore magna aliqua. Ut enim ad minim veniam, quis nostrud exercitation ullamco laboris nisi ut aliquip ex ea commodo consequat. Duis aute irure dolor in reprehenderit in voluptate velit esse cillum dolore eu fugiat nulla pariatur. Excepteur sint occaecat cupidatat non proident, sunt in culpa qui officia deserunt mollit anim id est laborum. Sed ut perspiciatis unde omnis iste natus error sit voluptatem accusantium doloremque laudantium, totam rem aperiam, eaque ipsa quae ab illo inventore veritatis et quasi architecto beatae vitae dicta sunt explicabo. Nemo enim ipsam voluptatem quia voluptas sit aspernatur aut odit aut.</p>
      <p>Lorem ipsum dolor sit amet, consectetur adipisicing elit, sed do eiusmod tempor incididunt ut labore et dolore magna aliqua. Ut enim ad minim veniam, quis nostrud exercitation ullamco laboris nisi ut aliquip ex ea commodo consequat. .</p>
    </section>

    <footer class="signature">
      <div class="signature-rule"></div>
      <div class="signature-name">Anselmo R Quintara III</div>
      <div class="signature-title">Attorney at Law</div>
      <ul class="contact-list">
        <li><svg viewBox="0 0 10 10"><path d="M2 0.5l2 2-1 1.2c.6 1.3 1.6 2.3 2.9 2.9L7 5.5l2.5 2-1 2C4.5 9.5.5 5.5.5 1.5z"/></svg>877-482-6017,</li>
        <li><svg viewBox="0 0 10 10"><rect x="2.5" y="0.5" width="5" height="3"/><rect x="0.5" y="3.5" width="9" height="4.5" rx="1"/><rect x="2.5" y="7" width="5" height="2.5"/></svg>469-738-1452</li>
        <li><svg viewBox="0 0 10 10"><path d="M0 2h10v6H0z M0 2l5 3.5L10 2" /></svg>bry@bry7legal.example</li>
        <li><svg viewBox="0 0 10 10"><path d="M5 0a5 5 0 1 0 0 10A5 5 0 0 0 5 0zm0 1.2a3.8 3.8 0 1 1 0 7.6 3.8 3.8 0 0 1 0-7.6z M1 5h8v.8H1z M4.6 1h.8v8h-.8z"/></svg>www.bry7legal.example</li>
        <li><svg viewBox="0 0 10 10"><path d="M5 0a3.4 3.4 0 0 1 3.4 3.4C8.4 6 5 10 5 10S1.6 6 1.6 3.4A3.4 3.4 0 0 1 5 0zm0 2a1.4 1.4 0 1 0 0 2.8A1.4 1.4 0 0 0 5 2z"/></svg>2847 Larkspur Blvd, Ste 300, Dallas, TX 75204</li>
      </ul>
    </footer>

    <div class="footer-band" aria-hidden="true">
      <div class="footer-band-main"></div>
      <div class="footer-band-accent"></div>
    </div>
  </main>
</body>
</html>
```